Food humor T-shirt and apparel company needs a Shopify site designed. We have logo files to help.

We are an apparel company based in Chicago by two cooking and food humor enthusiasts. We are looking for a redesign of our Shopify site. Our products are humorous quotes and pictures on shirts, sweaters and other apparel. The tagline for the company is - Find Your Yum. Wear Your Food. We want to see designs that incorporate our logo, brand color of royal purple, signify fun business casual clothing with amusing tags or images of trendy or esoteric food trends. The design should communicate excellence in taste but with maybe a satirical almost corporate type spin.
Target Market(s)
Hip, millennial foodies and cooks that love to try new foods, have great taste, and love to experiment in the restaurant or the kitchen.
Industry/Entity Type
Cooking
Look and feel
Each slider illustrates characteristics of the customer's brand and the style your logo design should communicate.

```html
<!DOCTYPE html>
<html lang="en">
<head>
<meta charset="utf-8">
<title>Savorwear — Find Your Yum. Wear Your Food.</title>
<link href="https://fonts.googleapis.com/css2?family=Lora:ital,wght@0,400;0,700;1,400;1,700&family=Roboto:wght@400;500&display=swap" rel="stylesheet">
<style>
:root{
  --purple:#5b2d8e;
  --purple-mid:#6a3d9a;
  --purple-soft:#7a4aa8;
  --ink:#222;
  --text:#444;
  --line:#e3e3e3;
  --card:#efefef;
  --orange:#e8441f;
  --dark:#1e1e1e;
}
*{box-sizing:border-box;margin:0;padding:0}
html,body{width:1200px;height:4267px;overflow:hidden}
body{position:relative;background:#fff;font-family:'Lora',serif;color:var(--text)}
.abs{position:absolute}
.topbar{left:0;top:0;width:1200px;height:33px;background:var(--purple);color:#fff;font:400 12px 'Roboto',sans-serif;display:flex;align-items:center;justify-content:center}
.topbar .close{position:absolute;right:90px;top:9px}
.currency{left:131px;top:101px;font-size:11px;color:var(--ink);display:flex;align-items:center;gap:14px}
.currency .select{border:1px solid #bbb;padding:3px 8px;font:400 11px 'Roboto',sans-serif;width:60px;display:flex;justify-content:space-between}
.brand{left:0;width:1200px;top:112px;text-align:center;font:700 34px 'Lora',serif;color:var(--purple)}
.brand-dot{left:585px;top:62px;width:30px;height:30px;border-radius:50%;background:var(--purple)}
.cartlinks{left:944px;top:70px;font-size:11px;color:var(--ink)}
.search{left:900px;top:101px;width:169px;height:32px;border:1px solid #ccc;font-size:11px;padding:8px 10px;color:#555}
.search svg{position:absolute;right:9px;top:9px}
.nav{left:0;top:190px;width:1200px;display:flex;justify-content:center;font-size:15px;color:var(--ink)}
.nav span{padding:0 21px;border-left:1px solid #ccc;line-height:16px}
.nav span:first-child{border-left:none}
.hr{left:0;top:236px;width:1200px;height:1px;background:var(--line)}
.hero{left:0;top:237px;width:1200px;height:560px;background:linear-gradient(90deg,#ecebe8,#e4e2de 70%,#d8d5d0)}
.hero-photo{left:620px;top:237px;width:300px;height:560px;background:linear-gradient(180deg,#d9cfc7 0%,#222 30%,#1b1b1b 75%,#3a3f55 100%);border-radius:120px 120px 0 0}
.hero-title{left:151px;top:382px;font:italic 700 104px/1 'Lora',serif;color:var(--purple);letter-spacing:1px}
.hero-sub{left:151px;top:502px;font:italic 400 29px 'Lora',serif;color:var(--ink)}
.btn{background:var(--dark);color:#fff;font:700 17px 'Lora',serif;display:flex;align-items:center;justify-content:center;gap:10px}
.hero-btn{left:151px;top:566px;width:166px;height:52px}
.arrow{width:33px;height:33px;border-radius:50%;background:#555;display:flex;align-items:center;justify-content:center}
.promo{top:867px;height:334px}
.h2{left:0;width:1200px;text-align:center;font:700 29px 'Lora',serif;color:var(--ink);letter-spacing:.5px}
.product{width:215px}
.product .img{height:247px;background:var(--card);border:1px solid #ddd}
.product .name{text-align:center;font-size:14px;line-height:23px;color:var(--ink);margin-top:15px}
.product .price{text-align:center;font:italic 400 17px 'Lora',serif;color:var(--purple);margin-top:10px}
.banner{left:132px;top:1816px;width:935px;height:416px;background:var(--purple-mid)}
.banner-photo{left:592px;top:1816px;width:475px;height:416px;background:radial-gradient(ellipse at 50% 55%,#151515 0 45%,var(--purple-soft) 70%)}
.banner-title{left:183px;top:1903px;font:italic 700 45px/52px 'Lora',serif;color:#fff}
.banner-sub{left:183px;top:2024px;font-size:19px;color:#fff}
.banner-btn{left:184px;top:2078px;width:163px;height:51px}
.post{width:292px;text-align:center}
.post .date{font:italic 400 15px 'Lora',serif;color:var(--purple)}
.post .title{font:700 15px/23px 'Lora',serif;color:var(--ink);margin-top:7px;height:46px;text-transform:uppercase}
.post .img{height:281px;margin-top:18px}
.post .body{font-size:12px;line-height:23px;color:var(--text);margin-top:18px;padding:0 6px}
.post .more{font:italic 400 12px 'Lora',serif;color:var(--purple);text-decoration:underline;margin-top:14px}
.video{left:132px;top:3024px;width:935px;height:481px;background:linear-gradient(180deg,#2d3138,#444b52 50%,#2a2d30)}
.video-shirt{left:420px;top:3090px;width:360px;height:415px;background:#9aa0a8;border-radius:90px 90px 0 0;opacity:.85}
.video-title{left:132px;top:3175px;width:935px;text-align:center;font:italic 700 44px/58px 'Lora',serif;color:#fff}
.play{left:578px;top:3303px;width:44px;height:44px;border-radius:50%;background:#fff;display:flex;align-items:center;justify-content:center}
.news{left:132px;top:3505px;width:935px;height:358px;border:2px solid var(--purple);border-top:none}
.news-title{left:0;width:1200px;top:3644px;text-align:center;font:400 40px/1.2 'Lora',serif;color:var(--ink)}
.news-sub{left:0;width:1200px;top:3706px;text-align:center;font-size:16px;color:var(--ink)}
.field{left:287px;top:3748px;width:626px;height:42px;border:1px solid #ddd;border-radius:21px;font-size:11px;color:#777;padding:13px 22px}
.subscribe{left:796px;top:3748px;width:117px;height:42px;border-radius:21px;background:var(--orange);color:#fff;font:700 13px 'Lora',serif;display:flex;align-items:center;justify-content:center}
.fcol{top:3935px;font-size:14px;line-height:28px;color:var(--ink)}
.fcol .i{display:flex;align-items:center;gap:10px}
.sq{width:12px;height:12px;background:var(--purple);border-radius:2px}
.chev{color:#555;font-size:13px}
.contact{left:727px;top:3928px;font-size:13px;color:var(--ink);line-height:21px}
.contact .row{display:flex;gap:16px;margin-bottom:14px}
.fline{left:132px;top:4114px;width:935px;height:1px;background:var(--line)}
.copy{left:132px;top:4165px;font-size:14px;color:var(--ink)}
.legal{left:132px;top:4193px;font-size:14px;color:var(--ink)}
.cards{left:890px;top:4178px;display:flex;gap:7px}
.cards span{width:39px;height:26px;border-radius:3px;border:1px solid #ccc}
</style>
</head>
<body>

<div class="abs topbar">Free shipping on all orders over $100 at checkout with the code 'SPRING'<span class="close">X</span></div>

<div class="abs currency">SELECT CURRENCY <span class="select">CAD <span>▾</span></span></div>
<div class="abs brand-dot"></div>
<div class="abs brand">Savorwear</div>
<div class="abs cartlinks">CART (0) &nbsp;CHECKOUT</div>
<div class="abs search">Search
  <svg width="13" height="13" viewBox="0 0 13 13"><circle cx="5.5" cy="5.5" r="4.2" fill="none" stroke="#222" stroke-width="1.8"/><line x1="8.6" y1="8.6" x2="12" y2="12" stroke="#222" stroke-width="2"/></svg>
</div>

<nav class="abs nav">
  <span>HOME</span><span>ABOUT SAVORWEAR</span><span>T-SHIRTS</span><span>SHOP</span><span>GIFT IDEAS</span><span>SAVORWEAR GIFTS</span><span>CONTACT US</span>
</nav>
<div class="abs hr"></div>

<section class="abs hero"></section>
<div class="abs hero-photo" role="img" aria-label="Bearded man in cap and sunglasses wearing a black food-pun t-shirt, leaning on a wall"></div>
<h1 class="abs hero-title">t-shirts</h1>
<div class="abs hero-sub">Find Your Yum. Wear Your Food</div>
<div class="abs btn hero-btn">SHOP NOW <svg width="14" height="14" viewBox="0 0 14 14"><path d="M1 7h11M7 2l5 5-5 5" stroke="#fff" stroke-width="2" fill="none"/></svg></div>
<div class="abs arrow" style="left:72px;top:487px"><svg width="12" height="14" viewBox="0 0 12 14"><path d="M8 2L3 7l5 5" stroke="#fff" stroke-width="2" fill="none"/></svg></div>
<div class="abs arrow" style="left:1095px;top:487px"><svg width="12" height="14" viewBox="0 0 12 14"><path d="M4 2l5 5-5 5" stroke="#fff" stroke-width="2" fill="none"/></svg></div>

<div class="abs promo" style="left:132px;width:463px;background:radial-gradient(ellipse at 50% 55%,#ffffff,#e6e3e0 70%)" role="img" aria-label="White mug printed with waffles and pancakes illustration"></div>
<div class="abs promo" style="left:603px;width:464px;background:linear-gradient(180deg,#efe7de 0%,#d8c2ad 35%,#2b2522 60%,#151515 100%)" role="img" aria-label="Woman wearing a black printed apron"></div>

<h2 class="abs h2" style="top:1283px">FEATURED PRODUCTS</h2>

<div class="abs product" style="left:132px;top:1377px"><div class="img" role="img" aria-label="Black t-shirt with round food illustration"></div><div class="name">Nemo enim ipsam<br>voluptatem quia voluptas sit</div><div class="price">$89.95</div></div>
<div class="abs product" style="left:372px;top:1377px"><div class="img" role="img" aria-label="Black tank top with ice cream print"></div><div class="name">Nemo enim ipsam<br>voluptatem quia voluptas sit</div><div class="price">$89.95</div></div>
<div class="abs product" style="left:613px;top:1377px"><div class="img" role="img" aria-label="White mug with cookie illustration"></div><div class="name">Nemo enim ipsam<br>voluptatem quia voluptas sit</div><div class="price">$89.95</div></div>
<div class="abs product" style="left:853px;top:1377px"><div class="img" role="img" aria-label="Grey t-shirt with pie pun print"></div><div class="name">Nemo enim ipsam<br>voluptatem quia voluptas sit</div><div class="price">$89.95</div></div>

<section class="abs banner"></section>
<div class="abs banner-photo" role="img" aria-label="Black sweater with ice cream cone illustration"></div>
<h3 class="abs banner-title">Premium<br>Printed sweaters</h3>
<div class="abs banner-sub">Sed ut perspiciatis unde omnis iste natus</div>
<div class="abs btn banner-btn">SHOP NOW <svg width="14" height="14" viewBox="0 0 14 14"><path d="M1 7h11M7 2l5 5-5 5" stroke="#fff" stroke-width="2" fill="none"/></svg></div>

<h2 class="abs h2" style="top:2310px">WHAT'S NEW</h2>

<article class="abs post" style="left:132px;top:2393px">
  <div class="date">October 17, 2019</div>
  <div class="title">I'm parched, let's drink:<br>Marlow Bar, Northside</div>
  <div class="img" role="img" aria-label="Two cocktails glowing by candlelight" style="background:linear-gradient(135deg,#2a0f0a,#8c2a18 45%,#d9733c 70%,#3a1a10)"></div>
  <div class="body">Show me a bartender that doesn't taste, and I show you cocktail that may not be worth your sips or your silver. The three brothers of the sultry, slinky Marlow dicta sunt explicabo. Nemo enim ipsam explicabo</div>
  <div class="more">Read more</div>
</article>
<article class="abs post" style="left:453px;top:2393px">
  <div class="date">October 17, 2019</div>
  <div class="title">Salted caramel apple<br>pie minis</div>
  <div class="img" role="img" aria-label="Lattice-topped mini apple pies" style="background:radial-gradient(circle at 50% 55%,#e6b36a,#c98a3c 40%,#6b4a3a 80%)"></div>
  <div class="body">Dearly Beloved, we are gathered here today to celebrate the union of salted caramel sauce and warm spiced apples. I present to you a recipe for a dessert marriage made in heaven: Salted Caramel Apple Pie Minis. Enjoy!</div>
  <div class="more">Read more</div>
</article>
<article class="abs post" style="left:775px;top:2393px">
  <div class="date">October 17, 2019</div>
  <div class="title">Just landed, let's eat: Lotus Cafe,<br>Chinatown, Chicago</div>
  <div class="img" role="img" aria-label="Plates of greens, rice and fried dishes on a table" style="background:linear-gradient(160deg,#4a5a3a,#a9a79a 40%,#e6e4df 60%,#b0773a)"></div>
  <div class="body">Hey, Boy. Take me to Lotus Cafe after midnight on that BYOB tip. You bring a DOCG Pinot Grigio and I'll raise you a bottle of the DOCG Chianti that I stowed in my checked bag. They will pair nicely with the Salt</div>
  <div class="more">Read more</div>
</article>

<section class="abs video" role="img" aria-label="Video still of a man in a grey food-pun t-shirt against a shutter"></section>
<div class="abs video-shirt"></div>
<div class="abs video-title">Find Your Yum.<br>Wear Your Food.</div>
<div class="abs play"><svg width="16" height="18" viewBox="0 0 16 18"><path d="M3 1l12 8-12 8z" fill="#222"/></svg></div>

<section class="abs news"></section>
<h4 class="abs news-title">Join our Newsletter</h4>
<div class="abs news-sub">Subscribe to our mailing list to receive updates and promotional offers.</div>
<div class="abs field">Enter your E - mail</div>
<div class="abs subscribe">SUBSCRIBE</div>

<div class="abs fcol" style="left:132px">
  <div class="i"><span class="sq"></span>Facepage</div>
  <div class="i" style="margin-top:6px"><span class="sq"></span>Chirper</div>
  <div class="i" style="margin-top:6px"><span class="sq"></span>Pinboard</div>
  <div class="i" style="margin-top:6px"><span class="sq"></span>Snapgram</div>
</div>
<div class="abs fcol" style="left:298px">
  <div class="i"><span class="chev">›</span>Cushions</div><div class="i"><span class="chev">›</span>t-shirts</div><div class="i"><span class="chev">›</span>Photo Panels</div><div class="i"><span class="chev">›</span>Gift Ideas</div><div class="i"><span class="chev">›</span>Novelty Gifts</div>
</div>
<div class="abs fcol" style="left:483px">
  <div class="i"><span class="chev">›</span>Search</div><div class="i"><span class="chev">›</span>Photo Panels</div><div class="i"><span class="chev">›</span>Passport Photography</div><div class="i"><span class="chev">›</span>Free Shipping Products</div><div class="i"><span class="chev">›</span>Contact</div>
</div>
<div class="abs contact">
  <div class="row"><svg width="16" height="20" viewBox="0 0 16 20"><path d="M8 1a6 6 0 0 0-6 6c0 5 6 12 6 12s6-7 6-12a6 6 0 0 0-6-6z" fill="none" stroke="var(--purple)" stroke-width="1.5"/><circle cx="8" cy="7" r="2" fill="var(--purple)"/></svg><div>14 Linden Row<br>Shop 3, Harbor Lane Arcade Riverton 4100</div></div>
  <div class="row"><svg width="16" height="16" viewBox="0 0 16 16"><path d="M3 1l3 3-2 2c1 2 3 4 5 5l2-2 3 3-2 3C7 14 2 9 1 3z" fill="none" stroke="var(--purple)" stroke-width="1.4"/></svg><div>Phone : &nbsp;05 5550 1928</div></div>
  <div class="row"><svg width="18" height="14" viewBox="0 0 18 14"><rect x="1" y="1" width="16" height="12" fill="none" stroke="var(--purple)" stroke-width="1.4"/><path d="M1 1l8 7 8-7" fill="none" stroke="var(--purple)" stroke-width="1.4"/></svg><div>Email : shop@savorwear.com</div></div>
</div>

<div class="abs fline"></div>
<div class="abs copy">©2019 Savorwear. All Rights Reserved.</div>
<div class="abs legal">Disclaimer &nbsp;| &nbsp;Privacy policy &nbsp;| &nbsp;Terms of use</div>
<div class="abs cards"><span style="background:#e9eef7"></span><span style="background:#2a2f6a"></span><span style="background:#1f4fa3"></span><span style="background:#f3e9a8"></span></div>

</body>
</html>
```